B2B modern industry lubrication label

We are a chemical company that needs a new, very modern outstanding lubrication packaging label. The logo attached can be changed in color. The name of the product is K72. Attached also the text you can use, please disregard the current layout of the text, you can make it any layout you want. Be free in font type, colors and other design aspects.
Dimensions: 21 x 14,8 cm
industry, companies with machinery
Industrial

```html
<!DOCTYPE html>
<html lang="en">
<head>
<meta charset="utf-8">
<title>HALDEN K72 Pro Lubricant Label</title>
<link rel="stylesheet" href="https://fonts.googleapis.com/css2?family=Arimo:wght@400;700&display=swap">
<style>
  :root {
    --backdrop: #1f5fcc;
    --frame: #a9b3b1;
    --label-black: #0b0c0c;
    --gold: #c9a35a;
    --divider: #8a9290;
  }
  * { margin: 0; padding: 0; box-sizing: border-box; }
  html, body {
    width: 1200px; height: 1200px; overflow: hidden;
    background: var(--backdrop);
    font-family: "Arimo", Arial, sans-serif;
  }
  .label {
    position: absolute; left: 105px; top: 60px;
    width: 990px; height: 1080px;
    background: var(--frame);
    padding: 17px 22px 17px 18px;
  }
  .label-body {
    display: flex; width: 100%; height: 100%;
    background: var(--label-black);
    color: var(--gold);
  }
  .front-panel {
    width: 472px; position: relative;
    border-right: 2px solid var(--divider);
    text-align: center;
  }
  .back-panel { flex: 1; position: relative; text-align: center; }
  .brand-name {
    font-weight: 700; letter-spacing: 1px; line-height: 1;
  }
  .front-panel .brand-name {
    position: absolute; top: 38px; left: 0; right: 0; font-size: 92px;
  }
  .product-name {
    position: absolute; top: 318px; left: 0; right: 0;
    font-weight: 700; font-size: 86px; line-height: 1; letter-spacing: 2px;
  }
  .product-type {
    position: absolute; top: 412px; left: 0; right: 0;
    font-weight: 700; font-size: 70px; line-height: 1; letter-spacing: 1px;
  }
  .tagline {
    position: absolute; top: 856px; left: 0; right: 0;
    font-size: 28px; line-height: 36px;
  }
  .volume {
    position: absolute; top: 974px; left: 0; right: 0; font-size: 18px;
  }
  .back-panel .brand-name {
    margin-top: 26px; font-size: 52px;
  }
  .copy {
    margin-top: 20px; font-size: 16.5px; line-height: 21px;
  }
  .copy h2 {
    font-size: 16.5px; font-weight: 400; margin-top: 16px;
  }
  .specs {
    display: inline-block; text-align: left; margin-top: 14px;
  }
</style>
</head>
<body>
  <section class="label">
    <div class="label-body">
      <div class="front-panel">
        <div class="brand-name">HALDEN</div>
        <h1 class="product-name">K72 Pro</h1>
        <div class="product-type">LUBRICANT</div>
        <p class="tagline">A High Grade Multifunctional<br>Product for Lubricant &amp; Protection</p>
        <p class="volume">500 ml</p>
      </div>
      <div class="back-panel">
        <div class="brand-name">HALDEN</div>
        <div class="copy">
          <p>K72 Pro is a high grade multifunctional product<br>
          for lubrication and protection product.<br>
          K72 Pro is composed out of high grade synthetic oils,<br>
          E.P. additives and penetrants.<br>
          Also the product contains<br>
          rust-preventing and waterproof substances.<br>
          Practical experience proofed that K72 Pro cleans,<br>
          lubricates and protects equipment, hinges,<br>
          cables, conveyer belts, chains and other moving parts<br>
          in machines and device excellently.<br>
          K72 Pro cleans fats, resins and rust on the surface<br>
          of materials. K72 Pro create a good<br>
          and durable lubrication.<br>
          Even under circumstances with extreme pressure.<br>
          K72 Pro protects against moisture and rust.</p>
          <h2>INSTRUCTIONS FOR USE:</h2>
          <p>•Short shake before use<br>
          •Spray a thin layer of K72 Pro on the surface.<br>
          The product will come out as a white,<br>
          fast disappearing foam.<br>
          •Let K72 Pro do its work for a few minutes.<br>
          •Own evaluation for necessity and result.</p>
          <h2>SPECIAL ADVANTAGES:</h2>
          <p>•K72 Pro drives off the eventually present moisture.<br>
          •K72 Pro can handle temperatures until 370°C.<br>
          •K72 Pro reaches even the smallest corners.<br>
          This is because of the pressure of the spray,<br>
          foaming and presence of high grade penetrants.<br>
          •K72 Pro forms an extremely thin<br>
          and smooth layer of grease (Fw value: 0,1).<br>
          •K72 Pro helps prevent "pitting wear".<br>
          •With use in propulsions,<br>
          the starting couple will be lowered.</p>
          <h2>SPECIFICATIONS:</h2>
          <p class="specs">Colour&nbsp; :&nbsp;&nbsp; Yellow<br>
          Density : 1,07 g/ml<br>
          Temperature range : -40 until 370 C</p>
        </div>
      </div>
    </div>
  </section>
</body>
</html>
```